Harborlight Plans (03)

We're designing a website to sell Medicare Supplements. Attached is the script we want to say and general layout, but please use your best knowledge to make it better. This platform should be extremely user-friendly, but we want to make it look fun and approachable! Most Insurance/medicare websites are very boring, drab, simple but we want this one to be more personalized, fun and sexy (but again, still user-friendly since our target demographic is 65+).

This homepage should include a fun and inviting quiz, the script is in the attachment below. It should also include the blurbs about what medicare supplements plans are and why they should buy them. Feel free to play around with cool fonts and imagery, we want the site to be engaging!

Target Market(s)

seniors

Industry/Entity Type

Insurance

Number of Pages Required

1 page

Requirements
Must have
• Quiz, company name and tag line, script
Nice to have
• fun, engaging elements

```html
<!DOCTYPE html>
<html lang="en">
<head>
<meta charset="utf-8">
<title>Harborlight Plans</title>
<link rel="stylesheet" href="https://fonts.googleapis.com/css2?family=Poppins:wght@400;500;600;700&family=Work+Sans:wght@400;500;600&display=swap">
<style>
:root{
  --red:#e8262b;
  --navy:#13254d;
  --navy-deep:#0f1e40;
  --ink:#1b1b1b;
  --text:#444;
  --grey-bg:#e6e6e6;
  --footer:#1a1a1a;
  --white:#fff;
}
*{margin:0;padding:0;box-sizing:border-box}
html,body{width:1200px;height:4144px;overflow:hidden}
body{position:relative;font-family:"Work Sans",sans-serif;color:var(--text);background:var(--white)}
.abs{position:absolute}
h1,h2,h3,h4,.head{font-family:"Poppins",sans-serif;color:var(--ink)}

/* header */
.site-header{position:absolute;left:0;top:0;width:1200px;height:116px;background:var(--white)}
.brand{left:145px;top:18px;display:flex;align-items:center;gap:14px}
.brand-mark{width:60px;height:60px;background:var(--navy)}
.brand-name{font-family:"Poppins",sans-serif;font-weight:700;font-size:28px;line-height:30px;color:var(--navy);letter-spacing:1px;text-transform:uppercase}
.call{left:636px;top:16px;display:flex;align-items:center;gap:10px}
.call small{display:block;font-size:13px;color:#555}
.call strong{font-family:"Poppins",sans-serif;font-size:20px;color:var(--navy);font-weight:600}
.btn-red{background:var(--red);color:var(--white);font-family:"Poppins",sans-serif;font-weight:600;border-radius:24px;text-align:center}
.header-btn{left:859px;top:14px;width:196px;height:46px;line-height:46px;font-size:15px;text-transform:uppercase}
.nav{right:145px;top:78px;display:flex;gap:28px;font-family:"Poppins",sans-serif;font-weight:600;font-size:16px;color:var(--navy)}

.hero{left:0;top:116px;width:1200px;height:463px;background:linear-gradient(90deg,#8b95a6 0%,#c7c3c4 45%,#b4aeb2 100%)}

/* quiz */
.quiz{left:0;top:579px;width:1200px;height:748px;background:var(--grey-bg)}
.quiz-title{position:absolute;top:58px;width:100%;text-align:center;font-family:"Poppins",sans-serif;font-weight:700;font-size:23px;color:var(--ink)}
.q-card{position:absolute;left:260px;width:679px;background:var(--white);box-shadow:0 3px 6px rgba(0,0,0,.15);padding:28px 0 0 74px}
.q-num{position:absolute;left:28px;top:30px;width:30px;height:30px;border-radius:50%;background:var(--red);color:var(--white);font-family:"Poppins",sans-serif;font-weight:700;font-size:14px;text-align:center;line-height:30px}
.q-card h3{font-size:19px;font-weight:500;margin-bottom:8px}
.q-card li{list-style:none;font-size:13px;line-height:18px;color:var(--ink)}
.zip{position:absolute;left:260px;top:578px;width:679px;height:61px;background:var(--white);box-shadow:0 3px 6px rgba(0,0,0,.15);padding-left:34px;line-height:61px;font-family:"Poppins",sans-serif;font-weight:500;font-size:20px;color:var(--ink)}
.zip-go{position:absolute;right:28px;top:12px;width:38px;height:38px;border-radius:50%;background:var(--red)}

/* about */
.about-title{left:145px;top:1416px;font-size:30px;font-weight:600;line-height:34px}
.rule{height:3px;width:62px;background:var(--red)}
.about-copy{left:145px;top:1526px;width:440px;font-size:13.5px;line-height:22.5px}
.ticks{left:145px;top:1680px;width:420px;font-size:13px;line-height:20px}
.ticks li{list-style:none;padding-left:18px;position:relative;margin-bottom:9px}
.ticks li::before{content:"✓";position:absolute;left:0;color:#2aa6c9}
.photo-frame{left:650px;top:1422px;width:406px;height:383px;border:3px solid var(--red)}
.about-photo{left:640px;top:1432px;width:407px;height:381px;background:linear-gradient(135deg,#c9b9a4,#6f7480 60%,#3c4d6d)}

/* costs */
.costs{left:0;top:1906px;width:1200px;height:698px;background:radial-gradient(ellipse at 50% 40%,#1d3464,var(--navy-deep) 75%)}
.costs h2{position:absolute;top:78px;width:100%;text-align:center;color:var(--white);font-weight:500;font-size:30px}
.costs .sub{position:absolute;left:145px;top:160px;width:910px;text-align:center;color:#dfe4ee;font-size:13.5px;line-height:22.5px}
.rate{position:absolute;top:264px;width:284px;height:278px;background:#f2f2f2;text-align:center;padding:30px 20px 0}
.rate h3{font-size:17px;font-weight:600;margin:16px 0 12px}
.rate p{font-size:13.5px;line-height:21px;color:var(--ink)}
.costs .note{position:absolute;left:300px;top:580px;width:600px;text-align:center;color:#dfe4ee;font-size:13.5px;line-height:22px}

/* news */
.news-title{left:0;top:2664px;width:1200px;text-align:center;font-size:40px;font-weight:600}
.news-rule{left:560px;top:2724px;width:80px;height:3px;background:var(--navy)}
.post{position:absolute;top:2773px;width:288px}
.post-img{height:200px}
.post .date{margin-top:28px;font-family:"Poppins",sans-serif;font-weight:500;font-size:13px;color:var(--ink);display:flex;align-items:center;gap:6px}
.post h4{margin-top:16px;font-size:13.5px;font-weight:600;line-height:20px;color:var(--navy);text-transform:uppercase}
.post p{margin-top:14px;font-size:13px;line-height:22.5px}
.post .more{margin-top:12px;font-family:"Poppins",sans-serif;font-weight:700;font-size:13px;color:var(--red)}

/* cta */
.cta{left:0;top:3364px;width:1200px;height:278px;background:linear-gradient(180deg,#1f3569,#1a3a8c)}
.cta h2{position:absolute;top:44px;width:100%;text-align:center;color:var(--white);font-weight:500;font-size:29px}
.cta-input{position:absolute;left:367px;top:111px;width:228px;height:48px;background:var(--white);display:flex;align-items:center;gap:10px;padding-left:16px;font-size:20px;color:var(--ink)}
.cta-btn{position:absolute;left:606px;top:111px;width:227px;height:48px;line-height:48px;background:var(--red);color:var(--white);text-align:center;font-family:"Poppins",sans-serif;font-weight:600;font-size:17px}
.cta .call-now{position:absolute;top:186px;width:100%;text-align:center;color:var(--white);font-size:20px}
.cta .call-now b{font-family:"Poppins",sans-serif;color:var(--red);font-size:24px;font-weight:600}

/* footer */
.footer{left:0;top:3642px;width:1200px;height:502px;background:var(--footer);color:#d8d8d8}
.footer h4{position:absolute;top:66px;color:var(--white);font-size:18px;font-weight:600;text-transform:uppercase}
.footer p,.footer li{font-size:13.5px;line-height:22.5px}
.f-col{position:absolute}
.f-item{display:flex;gap:16px;margin-bottom:14px}
.socials{display:flex;gap:6px;margin-top:18px}
.socials span{width:26px;height:26px;border:2px solid #ddd;border-radius:50%}
.email-box{width:272px;height:38px;background:var(--white);border-radius:20px;color:#777;font-size:12px;line-height:38px;padding-left:14px;margin-top:14px}
.subscribe{width:138px;height:34px;line-height:34px;font-size:15px;margin-top:10px;border-radius:18px}
.links li{list-style:none}
.copyright{position:absolute;top:440px;width:100%;text-align:center;font-size:13.5px}
</style>
</head>
<body>

<header class="site-header">
  <div class="abs brand">
    <div class="brand-mark"></div>
    <div class="brand-name">Harborlight<br>Plans</div>
  </div>
  <div class="abs call">
    <svg width="36" height="36" viewBox="0 0 24 24" fill="none" stroke="#e8262b" stroke-width="1.6"><path d="M5 3h4l2 5-2.5 1.5a11 11 0 0 0 6 6L16 13l5 2v4a2 2 0 0 1-2 2A16 16 0 0 1 3 5a2 2 0 0 1 2-2z"/></svg>
    <div><small>Call Us :</small><strong>(800) 555-0142</strong></div>
  </div>
  <div class="abs btn-red header-btn">Get Free Quotes</div>
  <nav class="abs nav"><span>HOME</span><span>ABOUT</span><span>MEDICARE</span><span>GET QUOTES</span><span>BLOG</span><span>CONTACT US</span></nav>
</header>

<div class="abs hero" role="img" aria-label="Smiling senior woman speaking with a care advisor"></div>

<section class="abs quiz">
  <h2 class="quiz-title">QUIZ SCRIPT:</h2>
  <div class="q-card" style="top:121px;height:140px"><span class="q-num">1.</span><h3>I am</h3><ul><li>a. Over 64 years old</li><li>b. 64 years old</li><li>c. Under 64 years old</li></ul></div>
  <div class="q-card" style="top:273px;height:141px"><span class="q-num">2.</span><h3>I am</h3><ul><li>a. Male</li><li>b. Female</li><li>c. Unspecified</li></ul></div>
  <div class="q-card" style="top:425px;height:140px"><span class="q-num">3.</span><h3>I want to see</h3><ul><li>a. Free plans</li><li>b. Premium plans</li><li>c. All plans</li></ul></div>
  <div class="zip">enter zip code
    <div class="zip-go"><svg width="38" height="38" viewBox="0 0 38 38"><path d="M12 20l15-8-6 15-2-5z" fill="#fff"/></svg></div>
  </div>
</section>

<h2 class="abs head about-title">What is a Medicare<br>Supplement plan?</h2>
<div class="abs rule" style="left:145px;top:1500px"></div>
<p class="abs about-copy">Each Medicare Supplement insurance plan offers a different level of basic benefits, but each lettered plan will include the same standardized basic benefits regardless of insurance company and location. Medicare Supplement insurance plans do not always cover vision, dental, long-term care, or hearing aids, but all plans must cover at least a portion of the following basic benefits:</p>
<ul class="abs ticks">
  <li>Medicare Part A coinsurance costs up to an additional 365 days after Medicare benefits are exhausted</li>
  <li>Medicare Part A hospice care coinsurance or copayments</li>
  <li>Medicare Part B coinsurance or copayments</li>
  <li>First three pints of blood used in a medical procedure</li>
</ul>
<div class="abs photo-frame"></div>
<div class="abs about-photo" role="img" aria-label="Excited senior couple celebrating in front of a laptop"></div>

<section class="abs costs">
  <h2>Medicare Supplement insurance plan costs</h2>
  <div class="abs rule" style="left:562px;top:136px;width:76px"></div>
  <p class="sub">Although private insurance companies are required to offer the same basic benefits for each lettered plan, they do have the ability to charge different premiums. You might want to shop around to find a Medicare Supplement insurance plan that may fit your medical and financial needs. Insurance companies may price their plan premiums in any of the following ways:</p>
  <div class="rate" style="left:143px">
    <svg width="62" height="62" viewBox="0 0 62 62" fill="none" stroke="#e8262b" stroke-width="2.5"><path d="M31 6a24 22 0 1 1-14 40L6 54l4-12A24 22 0 0 1 31 6z"/><path d="M20 24h22M20 31h22M20 38h14"/></svg>
    <h3>Community no-age-rated:</h3>
    <p>These Medicare Supplement insurance plans charge premiums that are the same across the board, regardless of age.</p>
  </div>
  <div class="rate" style="left:457px">
    <svg width="62" height="62" viewBox="0 0 62 62" fill="none" stroke="#e8262b" stroke-width="2.5"><circle cx="18" cy="10" r="5"/><path d="M12 56V22h12v34M30 56V34h8v22M8 56h30"/><circle cx="48" cy="42" r="10"/><path d="M48 36v12"/></svg>
    <h3>Issue-age-rated:</h3>
    <p>These plans base their premiums on your age when you first enrolled in the policy. Therefore, the younger you are when you enroll in this type of plan, the lower your premium will be.</p>
  </div>
  <div class="rate" style="left:772px">
    <svg width="62" height="62" viewBox="0 0 62 62" fill="none" stroke="#e8262b" stroke-width="2.5"><path d="M10 6h32v50H10z"/><path d="M17 16h18M17 24h18M17 32h12M17 40h10"/><path d="M52 14l-16 30-4 6 1-7 16-30z"/></svg>
    <h3>Attained-age-rated:</h3>
    <p>Like issue-age-rated, these plans base their premiums on the age you were when you first bought a policy, but unlike issue-age-rated, premiums increase as you get older</p>
  </div>
  <p class="note">Please note that no matter what rating method an insurance company uses, premiums may increase over time for reasons other than age, such as inflation.</p>
</section>

<h2 class="abs head news-title">Latest News</h2>
<div class="abs news-rule"></div>
<article class="post" style="left:135px">
  <div class="post-img" role="img" aria-label="Caregiver helping a senior woman at home" style="background:linear-gradient(135deg,#d9d3c6,#7d8a99)"></div>
  <div class="date"><svg width="12" height="12" viewBox="0 0 12 12"><rect x="1" y="2" width="10" height="9" fill="none" stroke="#333" stroke-width="1.4"/><path d="M1 5h10" stroke="#333"/></svg>UPDATED: MARCH 09, 2020</div>
  <h4>Nemo enim ipsam voluptatem quia voluptas sit</h4>
  <p>Sed ut perspiciatis unde omnis iste natus error sit voluptatem accusantium dremque laudantium, totam rem aperiam, eaque ipsa quae ab illo inventore veritatis et quasi architecto beatae vitae dicta sunt explicabo. Nemo enim ipsam voluptatem quia voluptas sit aspernatur aut odit aut fugit, sed quia consequuntur</p>
  <div class="more">LEARN MORE →</div>
</article>
<article class="post" style="left:455px">
  <div class="post-img" role="img" aria-label="Senior couple meeting with an advisor" style="background:linear-gradient(135deg,#cfcfcf,#6e7378)"></div>
  <div class="date"><svg width="12" height="12" viewBox="0 0 12 12"><rect x="1" y="2" width="10" height="9" fill="none" stroke="#333" stroke-width="1.4"/><path d="M1 5h10" stroke="#333"/></svg>UPDATED: MARCH 09, 2020</div>
  <h4>Nemo enim ipsam voluptatem quia voluptas sit</h4>
  <p>Sed ut perspiciatis unde omnis iste natus error sit voluptatem accusantium dremque laudantium, totam rem aperiam, eaque ipsa quae ab illo inventore veritatis et quasi architecto beatae vitae dicta sunt explicabo. Nemo enim ipsam voluptatem quia voluptas sit aspernatur aut odit aut fugit, sed quia consequuntur</p>
  <div class="more">LEARN MORE →</div>
</article>
<article class="post" style="left:775px">
  <div class="post-img" role="img" aria-label="Senior couple relaxing on a sofa with a laptop" style="background:linear-gradient(135deg,#e3ddd2,#8c98a8)"></div>
  <div class="date"><svg width="12" height="12" viewBox="0 0 12 12"><rect x="1" y="2" width="10" height="9" fill="none" stroke="#333" stroke-width="1.4"/><path d="M1 5h10" stroke="#333"/></svg>UPDATED: MARCH 09, 2020</div>
  <h4>Nemo enim ipsam voluptatem quia voluptas sit</h4>
  <p>Sed ut perspiciatis unde omnis iste natus error sit voluptatem accusantium dremque laudantium, totam rem aperiam, eaque ipsa quae ab illo inventore veritatis et quasi architecto beatae vitae dicta sunt explicabo. Nemo enim ipsam voluptatem quia voluptas sit aspernatur aut odit aut fugit, sed quia consequuntur</p>
  <div class="more">LEARN MORE →</div>
</article>

<section class="abs cta">
  <h2>Get a Free Harborlight Plans Quote</h2>
  <div class="cta-input"><svg width="16" height="20" viewBox="0 0 16 20" fill="none" stroke="#e8262b" stroke-width="2"><path d="M8 19s7-7 7-11A7 7 0 0 0 1 8c0 4 7 11 7 11z"/><circle cx="8" cy="8" r="2.5"/></svg>60003</div>
  <div class="cta-btn">Get FREE Quotes</div>
  <div class="call-now">Call Now <b>(800) 555-0142</b></div>
</section>

<footer class="abs footer">
  <h4 style="left:145px">About Us</h4>
  <div class="f-col" style="left:145px;top:120px;width:190px">
    <p>Sed ut perspiciatis unde omnis iste natus error sit vtem accusantium dremque lam, totam rem aperiam, eaque ipsa quae ab illo intore veritatis et quasi acto beatae vitae dicta</p>
    <div class="socials"><span></span><span></span><span></span><span></span></div>
  </div>
  <h4 style="left:357px">Contact Us</h4>
  <div class="f-col" style="left:357px;top:124px;width:240px">
    <div class="f-item"><svg width="16" height="20" viewBox="0 0 16 20" fill="#fff"><path d="M8 19s7-7 7-11A7 7 0 0 0 1 8c0 4 7 11 7 11zm0-8a3 3 0 1 0 0-6 3 3 0 0 0 0 6z"/></svg><p>Harborlight Plans Suite 210 Austin, Texas 78701</p></div>
    <div class="f-item"><svg width="16" height="16" viewBox="0 0 24 24" fill="#fff"><path d="M5 3h4l2 5-2.5 1.5a11 11 0 0 0 6 6L16 13l5 2v4a2 2 0 0 1-2 2A16 16 0 0 1 3 5a2 2 0 0 1 2-2z"/></svg><p>P.808.555.0127<br>F.808.555.0188</p></div>
    <div class="f-item"><svg width="16" height="14" viewBox="0 0 16 14" fill="#fff"><path d="M0 1h16v12H0z"/><path d="M0 1l8 6 8-6" stroke="#1a1a1a" stroke-width="1.5" fill="none"/></svg><p>Email:<br>info@harborlightplans.com</p></div>
  </div>
  <h4 style="left:616px">Sign up for newsletter</h4>
  <div class="f-col" style="left:616px;top:120px;width:290px">
    <p>excepteur sint occaecat cupidatat non proident, sunt in culpa qui officia deserunt</p>
    <div class="email-box">Enter email</div>
    <div class="btn-red subscribe">SUBSCRIBE</div>
  </div>
  <h4 style="left:931px">Quick Links</h4>
  <ul class="f-col links" style="left:935px;top:114px"><li>Home</li><li>About Us</li><li>Medicare</li><li>Get Quotes</li><li>Blog</li></ul>
  <p class="copyright">Harborlight Plans © 2020 All Rights Reserved | Privacy Policy | Terms and Conditions</p>
</footer>

</body>
</html>
```